Maplecrest Disability - Social Security Disability Attorneys

Our company is expanding to attract clients nationwide for our social security disability practice. We have a logo, but I am looking for a creative and elegant letterhead that projects an image of being technologically advanced but still professional enough for the legal field. I am looking for the "wow factor" combined with this is still professional enough for a law practice.

Requesting letterhead and business card design
Updates

Had to update and change the logo. The previous logo had a typo. Please send updates with the new logo for consideration. The letterhead and business cards should be professional enough to be used for a law firm. Thanks.

Industry/Entity Type

Law Practice, Law Firm, Healthcare Industry, Government

Colors

Designer to choose colors to be used in the design.

Requirements
Nice to have
• **Please create a vertical design for the business card**

```html
<!DOCTYPE html>
<html lang="en">
<head>
<meta charset="utf-8">
<title>Maplecrest Disability – Business Card</title>
<link rel="stylesheet" href="https://fonts.googleapis.com/css2?family=Montserrat:wght@500;600;800&display=swap">
<style>
  :root {
    --stage: #229ed9;
    --brand-blue: #546fb6;
    --brand-orange: #f5821f;
    --ink: #1c1c1c;
    --paper: #ffffff;
  }
  * { margin: 0; padding: 0; box-sizing: border-box; }
  html, body { width: 1200px; height: 1128px; overflow: hidden; background: var(--stage); }
  .stage { position: relative; width: 1200px; height: 1128px; }
  .card {
    position: absolute; top: 129px; height: 868px;
    border-radius: 36px; overflow: hidden;
    font-family: "Montserrat", sans-serif;
  }
  .card--back { left: 70px; width: 501px; background: var(--brand-blue); color: var(--paper); }
  .card--front { left: 633px; width: 496px; background: var(--paper); color: var(--ink); }
  .row {
    position: absolute; left: 0; right: 0; text-align: center;
    transform: translateY(-50%);
  }
  .brand-dot {
    width: 26px; height: 26px; border-radius: 50%;
    background: var(--brand-orange); margin: 0 auto;
  }
  .brand-name {
    font-weight: 600; font-size: 28px; white-space: nowrap;
  }
  .brand-tagline {
    font-weight: 600; font-size: 12px; white-space: nowrap;
  }
  .card--front .brand-name,
  .card--front .brand-tagline { color: var(--brand-blue); }
  .industries { font-size: 20px; font-weight: 500; line-height: 31px; }
  .person-name {
    font-weight: 800; font-size: 29px; color: var(--brand-orange); letter-spacing: -0.3px;
  }
  .person-role {
    display: flex; align-items: center; justify-content: center; gap: 6px;
    font-size: 21px; font-weight: 500;
  }
  .person-role::before, .person-role::after {
    content: ""; width: 66px; height: 2px; background: var(--brand-orange);
  }
  .address { font-size: 19px; font-weight: 500; line-height: 29px; }
  .contact-icons { display: flex; justify-content: center; gap: 34px; }
  .contact-icons svg { width: 22px; height: 22px; fill: var(--brand-orange); }
  .contact-line { font-size: 19px; font-weight: 500; }
  .wave { position: absolute; inset: 0; width: 100%; height: 100%; }
</style>
</head>
<body>
<div class="stage">

  <section class="card card--back">
    <div class="row" style="top:378px"><div class="brand-dot"></div></div>
    <div class="row brand-name" style="top:420px">Maplecrest Disability</div>
    <div class="row brand-tagline" style="top:446px">Social Security Disability Attorneys</div>
    <div class="row industries" style="top:731px">Law Practice, Law Firm,<br>Healthcare Industry, Government</div>
  </section>

  <section class="card card--front">
    <svg class="wave" viewBox="0 0 496 868" preserveAspectRatio="none" aria-hidden="true">
      <path d="M0 794 C30 784 60 780 80 780 C180 780 280 831 367 831 C420 831 460 818 496 803 L496 868 L0 868 Z" fill="var(--brand-blue)"/>
      <path d="M0 794 C30 784 60 780 80 780 C180 780 280 831 367 831 C420 831 460 818 496 803" fill="none" stroke="var(--brand-orange)" stroke-width="5"/>
    </svg>

    <div class="row" style="top:141px"><div class="brand-dot"></div></div>
    <div class="row brand-name" style="top:195px">Maplecrest Disability</div>
    <div class="row brand-tagline" style="top:221px">Social Security Disability Attorneys</div>

    <div class="row person-name" style="top:327px">DANIEL WHITFORD</div>
    <div class="row person-role" style="top:360px">Co-Founder</div>

    <div class="row address" style="top:474px">Suite 4, Level 12, Harbour<br>Street Sydney NSW 2000</div>

    <div class="row contact-icons" style="top:562px">
      <svg viewBox="0 0 24 24" aria-label="Phone"><path d="M6.6 10.8a15.1 15.1 0 0 0 6.6 6.6l2.2-2.2c.3-.3.7-.4 1-.2 1.1.4 2.3.6 3.6.6.6 0 1 .4 1 1V20c0 .6-.4 1-1 1A17 17 0 0 1 3 4c0-.6.4-1 1-1h3.5c.6 0 1 .4 1 1 0 1.3.2 2.5.6 3.6.1.3 0 .7-.2 1z"/></svg>
      <svg viewBox="0 0 24 24" aria-label="Email"><path d="M2 5h20v14H2z"/><path d="M3 6l9 7 9-7" fill="none" stroke="#fff" stroke-width="1.5"/></svg>
      <svg viewBox="0 0 24 24" aria-label="Website"><circle cx="12" cy="12" r="10"/><path d="M2 12h20M12 2c3 3 3 17 0 20M12 2c-3 3-3 17 0 20" fill="none" stroke="#fff" stroke-width="1.3"/></svg>
    </div>

    <div class="row contact-line" style="top:619px">555-210-4870</div>
    <div class="row contact-line" style="top:653px">Info@maplecrestdisability.com</div>
    <div class="row contact-line" style="top:685px">www.maplecrestdisability.com</div>
  </section>

</div>
</body>
</html>
```